Business Card Design

My business is writing crime novels to entertain readers. I write legal thrillers and mysteries. I need a card for publishers, agents, other authors, and media.

Industry/Entity Type

Legal

Contact Information for Business Card

Paul Derrow
www.derrowfiction.example
pauljderrow@inkpost.example
0064 27 5190472

```html
<!DOCTYPE html>
<html lang="en">
<head>
<meta charset="utf-8">
<title>Paul Derrow – Business Card</title>
<link rel="stylesheet" href="https://fonts.googleapis.com/css2?family=Montserrat:wght@800&family=Ubuntu:wght@400;500&display=swap">
<style>
  :root {
    --stage: #e9e7e4;
    --card: #ffffff;
    --ink: #111111;
    --grey-text: #6b6b6b;
    --red: #e8392b;
    --red-dark: #c9241a;
    --orange: #f2643a;
    --photo-light: #8c8c8c;
    --photo-dark: #6f6f6f;
    --shirt: #2b2b2b;
  }
  html, body {
    margin: 0;
    width: 1200px;
    height: 873px;
    overflow: hidden;
    background: var(--stage);
  }
  .stage {
    position: relative;
    width: 1200px;
    height: 873px;
  }
  .card {
    position: absolute;
    left: 240px;
    top: 206px;
    width: 720px;
    height: 460px;
    background: var(--card);
    overflow: hidden;
    box-shadow: 0 6px 24px rgba(0,0,0,0.18);
  }
  .portrait {
    position: absolute;
    left: 0; top: 0;
    width: 720px; height: 200px;
    background: linear-gradient(180deg, var(--photo-light) 0%, var(--photo-dark) 100%);
  }
  .divider-band {
    position: absolute;
    left: 0; top: 200px;
    width: 720px; height: 14px;
    background: linear-gradient(90deg, var(--red-dark), var(--red) 50%, var(--orange));
  }
  .author-name {
    position: absolute;
    right: 40px; top: 236px;
    margin: 0;
    font-family: "Montserrat", sans-serif;
    font-weight: 800;
    font-size: 40px;
    letter-spacing: 1px;
    color: var(--ink);
    text-transform: uppercase;
  }
  .genre-band {
    position: absolute;
    left: 360px; top: 294px;
    width: 360px; height: 70px;
    background: linear-gradient(90deg, var(--red-dark), var(--red) 55%, var(--orange));
    box-sizing: border-box;
    padding: 11px 0 0 22px;
    font-family: "Ubuntu", sans-serif;
    font-weight: 400;
    font-size: 20px;
    line-height: 24px;
    letter-spacing: 1px;
    color: #fff;
    text-transform: uppercase;
  }
  .contact-list {
    position: absolute;
    left: 240px; top: 378px;
    margin: 0; padding: 0;
    list-style: none;
    font-family: "Ubuntu", sans-serif;
    font-size: 19px;
    line-height: 25px;
    color: var(--grey-text);
  }
  .contact-list li {
    display: flex;
    align-items: center;
    gap: 10px;
  }
  .contact-icon {
    width: 16px; height: 16px;
    flex: none;
  }
</style>
</head>
<body>
<main class="stage">
  <article class="card">
    <div class="portrait" role="img" aria-label="Studio portrait of the author in a dark jacket against a grey backdrop"></div>
    <div class="divider-band"></div>

    <h1 class="author-name">Paul Derrow</h1>
    <div class="genre-band">Legal thrillers<br>and mysteries writing</div>

    <ul class="contact-list">
      <li>
        <svg class="contact-icon" viewBox="0 0 16 16" aria-hidden="true">
          <rect x="4" y="1" width="8" height="14" rx="1.5" fill="var(--red)"/>
          <rect x="5.5" y="3" width="5" height="7" fill="#fff"/>
          <circle cx="8" cy="12.5" r="1" fill="#fff"/>
        </svg>
        <span>0064 27 5190472</span>
      </li>
      <li>
        <svg class="contact-icon" viewBox="0 0 16 16" aria-hidden="true">
          <rect x="1" y="3.5" width="14" height="9" rx="1" fill="var(--red)"/>
          <path d="M1.5 4 L8 9 L14.5 4" fill="none" stroke="#fff" stroke-width="1.3"/>
        </svg>
        <span>pauljderrow@inkpost.example</span>
      </li>
      <li>
        <svg class="contact-icon" viewBox="0 0 16 16" aria-hidden="true">
          <circle cx="8" cy="8" r="7" fill="var(--red)"/>
          <g fill="none" stroke="#fff" stroke-width="1">
            <ellipse cx="8" cy="8" rx="3" ry="6.5"/>
            <line x1="1.5" y1="8" x2="14.5" y2="8"/>
            <line x1="8" y1="1.5" x2="8" y2="14.5"/>
          </g>
        </svg>
        <span>www.derrowfiction.example</span>
      </li>
    </ul>
  </article>
</main>
</body>
</html>
```